Firearms Retailer Needs a Business Card Design

I am a firearms and sporting goods retailer in need of a business card design. I am looking for something cool and edgy, but that still looks professional. I would like something unique on the back like a ballistics chart, or something like the image I uploaded. I would certainly like other suggestions, maybe even something funny or unique. Please be creative. Please use the logo somewhere on the front of the card. My business name is Harrow Sporting Co.. My website is www.harrowsporting.com. I would like the following verse worked into the design inconspicuously, if possible: “No weapon forged against you will prevail, and you will refute every tongue that accuses you. This is the heritage of the servants of the Lord, and this is their vindication from me,” declares the Lord. Orvane 32:9. It may need to be worked in on the back, or possibly in very small font as a border on the front of the card. Again, please be creative.

```html
<!DOCTYPE html>
<html lang="en">
<head>
<meta charset="utf-8">
<title>Harrow Sporting Co. — Business Card</title>
<link rel="stylesheet" href="https://fonts.googleapis.com/css2?family=Open+Sans:wght@400;600;700&display=swap">
<style>
  :root {
    --page-bg: #e9e6e2;
    --card-bg: #ffffff;
    --accent-red: #d8272b;
    --name-red: #e0474a;
    --ink: #2b2b2b;
    --muted: #555555;
    --verse-grey: #a9a9a9;
    --card-shadow: rgba(0, 0, 0, 0.18);
  }
  * { box-sizing: border-box; margin: 0; padding: 0; }
  html, body {
    width: 1200px;
    height: 913px;
    overflow: hidden;
    background: var(--page-bg);
    font-family: "Open Sans", Arial, sans-serif;
    color: var(--ink);
  }
  .canvas {
    position: relative;
    width: 1200px;
    height: 913px;
    display: flex;
    align-items: center;
    justify-content: center;
    gap: 40px;
  }
  .card {
    position: relative;
    width: 540px;
    height: 309px;
    background: var(--card-bg);
    box-shadow: 0 8px 24px var(--card-shadow);
  }
  .wordmark {
    display: flex;
    align-items: center;
    gap: 10px;
    font-weight: 700;
    color: var(--ink);
    white-space: nowrap;
  }
  .wordmark-mark {
    background: var(--ink);
    flex: none;
  }
  .card-front {
    display: flex;
    align-items: center;
    justify-content: center;
  }
  .card-front .wordmark { font-size: 38px; }
  .card-front .wordmark-mark { width: 18px; height: 18px; }

  .card-back .wordmark {
    position: absolute;
    left: 30px;
    top: 142px;
    font-size: 20px;
  }
  .card-back .wordmark-mark { width: 11px; height: 11px; }

  .contact {
    position: absolute;
    left: 292px;
    top: 44px;
    width: 232px;
  }
  .contact-name {
    font-size: 20px;
    font-weight: 700;
    color: var(--name-red);
    line-height: 1.1;
  }
  .contact-role {
    font-size: 11px;
    color: var(--muted);
    margin-bottom: 8px;
  }
  .contact-list { list-style: none; }
  .contact-item {
    display: flex;
    align-items: flex-start;
    gap: 8px;
    font-size: 11.5px;
    line-height: 1.25;
    color: var(--ink);
    margin-bottom: 4px;
  }
  .contact-icon {
    width: 12px;
    height: 12px;
    flex: none;
    margin-top: 1px;
    fill: var(--accent-red);
  }
  .verse {
    position: absolute;
    left: 30px;
    right: 30px;
    bottom: 26px;
    font-size: 8.5px;
    line-height: 1.4;
    color: var(--verse-grey);
    text-align: right;
  }
</style>
</head>
<body>
<main class="canvas">

  <section class="card card-front" aria-label="Business card front">
    <div class="wordmark"><span class="wordmark-mark"></span>Harrow Sporting Co.</div>
  </section>

  <section class="card card-back" aria-label="Business card back">
    <div class="wordmark"><span class="wordmark-mark"></span>Harrow Sporting Co.</div>

    <div class="contact">
      <h1 class="contact-name">Your Name</h1>
      <p class="contact-role">Director</p>
      <ul class="contact-list">
        <li class="contact-item">
          <svg class="contact-icon" viewBox="0 0 12 12" aria-hidden="true"><path d="M6 0a4 4 0 0 0-4 4c0 3 4 8 4 8s4-5 4-8a4 4 0 0 0-4-4zm0 5.6A1.6 1.6 0 1 1 6 2.4a1.6 1.6 0 0 1 0 3.2z"/></svg>
          <span>Your commercial address in just<br>two line</span>
        </li>
        <li class="contact-item">
          <svg class="contact-icon" viewBox="0 0 12 12" aria-hidden="true"><path d="M1 4c0-1.5 2.2-2.5 5-2.5S11 2.5 11 4v1H8.5V4h-5v1H1z"/><rect x="2.5" y="5.5" width="7" height="5" rx="1"/></svg>
          <span>00000000000</span>
        </li>
        <li class="contact-item">
          <svg class="contact-icon" viewBox="0 0 12 12" aria-hidden="true"><path d="M0 2h12v8H0z M0 2l6 4.5L12 2" stroke="#fff" stroke-width="0.8"/></svg>
          <span>yourname@www.harrowsporting.com</span>
        </li>
        <li class="contact-item">
          <svg class="contact-icon" viewBox="0 0 12 12" aria-hidden="true"><circle cx="6" cy="6" r="5.5"/><path d="M0.5 6h11M6 0.5c-2.4 3-2.4 8 0 11M6 0.5c2.4 3 2.4 8 0 11" stroke="#fff" stroke-width="0.7" fill="none"/></svg>
          <span>www.www.harrowsporting.com</span>
        </li>
      </ul>
    </div>

    <p class="verse">No weapon forged against you will prevail, and you will refute every tongue that accuses you. This is the heritage of the servants of the Lord, and this is their vindication from me.</p>
  </section>

</main>
</body>
</html>
```